One of Australia's fastest growing energy maintenance contractors needs a new website

www.brightleaf.com.au
Our business has evolved over the past years and now our website is no longer relevant.
We clean solar panels and we vacuum roof gutters.
We clean solar panels on the roofs of residential houses right up to billion dollar solar farms with in excess of 1 million panels. We offer thermal image testing and bird proofing for our residential and commercial clients and thermal drone imaging services for our solar farm clients.
We vacuum clean roof gutters (using a LoftSuck) on the residential house next door right up to enormous private and public schools, colleges, shopping centres, strat complexes and commercial buildings.
When first built our business had more of a domestic residential skew and the website reflected that. While that is still part of our core business we are now bidding on and have secured large government, commercial and infrastructure contracts and our new website needs to reflect our growth and our new business. We need a new site that it optimised for both desktop ad phone viewing as our latest figures showed that 73% of people visiting our site are on mobile phones. We have an extensive amount of data on Tallymark Insights available as well as Bidlines. Both that would also need integrating with the site along with a few other plugins such as Quilro Chat IQ, Chatterbox etc along with SEO key words etc. We are also the winner and finalists over multiple years of the small business of the year awards and we like to proudly and prominently display those on our site.
We are looking for a new site with a modern professional feel / theme
There is a definitive break in our business between the solar Panel cleaning clients and the gutter cleaning clients so we would like a home page that begins with a simple choice:
Solar Panel Cleaning – Gutter Cleaning
With a professional full screen background image (we have hundreds to choose from) and along the bottom a small area with rights reserved etc, phone number etc (at some point in the future we will split these into two businesses but for now it’s what we have).
After that selection is made we would like a repeat of that same scenario but the selection is:
If it’s Solar Panel Cleaning
(new background image)
Government – Infrastructure – Commercial – Residential
If it’s Gutter Cleaning
(new background image)
Government – Strata – Commercial – Residential
After making those choices then onto the relevant pages with background images relevant to each sector and a them that suits (on the residential we would like to keep the link to our tallymark reviews) - We will provide copy / text for each relevant page.
Other than that, a menu inclusive of the above and:
Resellers Portal – we will provide a link to this from Quilro CRM)
Customer portal (we will supply a link to this from our booking system)
We also need a page for our Solar Resellers / Partners page but we will give them a link to this, it won’t be listed on the site.
Request a quote page (Again we will provide information from Quilro as this will be linked to the CRM)
Standard contact us page inclusive of phone numbers, address and fields supplied from CRM
Sydney – 02 7391 8056
Southern Highlands – 02 4863 1708
Goulburn – 02 4863 1708
Canberra – 02 6172 4385
Wollongong – 02 4239 5817
sales@brightleaf.com.au
Head Office - Kestrel Vale NSW 2580
ABN: 48093716552
Responsive Design: Optimized for desktop and mobile (73% mobile visitors).
Fast Loading Speed: Optimized for performance.
Smooth Transition Animations: For service and category selection.
Sticky Contact Bar: Always accessible at the bottom of mobile screens for quick calls.
SEO Optimization: Focused on government tenders, large-scale commercial contracts, and infrastructure projects.
Integrations
Tallymark Insights & Tallymark Bidlines.
Quilro Chat IQ.
Chatterbox Beacon.
SEO tools and keyword optimization.
Many many more images available if needed
Target Market(s)
Residential, commercial, Government

```html
<!DOCTYPE html>
<html lang="en">
<head>
<meta charset="utf-8">
<title>Brightleaf – Website Screens</title>
<link href="https://fonts.googleapis.com/css2?family=Poppins:wght@400;500;600;700&display=swap" rel="stylesheet">
<style>
:root{
  --page:#f7f7f7;
  --ink:#111418;
  --white:#ffffff;
  --blue:#1a7fd4;
  --blue-deep:#0b5fae;
  --blue-light:#e6f3fc;
  --footer:#000000;
  --number:#eef0f2;
}
*{margin:0;padding:0;box-sizing:border-box}
html,body{width:1200px;height:904px;overflow:hidden;background:var(--page);font-family:"Poppins",sans-serif;color:var(--ink)}
.board{position:relative;width:1200px;height:904px}
.screen{position:absolute;width:546px;height:390px;overflow:hidden;background:var(--footer);box-shadow:0 8px 28px rgba(0,0,0,.14)}
.screen--home{left:35px;top:47px}
.screen--gutter{left:618px;top:47px}
.screen--solar{left:618px;top:468px}
.hero{position:absolute;left:0;top:0;width:546px;height:269px;overflow:hidden}
.photo{position:absolute;inset:0}
.photo--solar-field{background:linear-gradient(180deg,#6f8da0 0%,#d9a25a 28%,#f2b458 40%,#5d5a48 52%,#2a3a4e 70%,#1b2533 100%)}
.photo--roof{background:linear-gradient(160deg,#3d5a78 0%,#24394f 45%,#1a2839 75%,#6b4a2a 100%)}
.photo--autumn{background:radial-gradient(ellipse at 50% 30%,#f0a040 0%,#b05e1c 30%,#4a2c18 60%,#1e2d3e 100%)}
.photo--split-right{clip-path:polygon(58% 0,100% 0,100% 100%,42% 100%)}
.hero-shade{position:absolute;inset:0;background:linear-gradient(180deg,rgba(0,0,0,.05),rgba(0,0,0,.25))}
.hero-mark{position:absolute;left:50%;transform:translateX(-50%)}
.hero-mark .square{display:block;width:14px;height:14px;background:var(--blue)}
.hero-mark--white .square{background:var(--white)}
.hero-title{position:absolute;left:0;width:100%;text-align:center;color:var(--white);font-weight:700;line-height:1.2;text-shadow:0 2px 6px rgba(0,0,0,.35)}
.hero-sub{position:absolute;left:0;width:100%;text-align:center;color:var(--white);font-weight:500;font-size:11px;line-height:1.4;text-shadow:0 1px 4px rgba(0,0,0,.5)}
.choice-card{position:absolute;background:var(--white);height:67px;box-shadow:0 4px 10px rgba(0,0,0,.2)}
.choice-card .num{position:absolute;font-weight:700;font-size:15px;color:var(--number)}
.choice-card .label{position:absolute;font-weight:600;font-size:7.2px;color:var(--ink);letter-spacing:.1px;white-space:nowrap}
.choice-card .more{position:absolute;font-size:4.6px;color:var(--blue);text-decoration:underline;white-space:nowrap}
.corner{position:absolute;width:16px;height:16px;z-index:3}
.corner--tl{background:linear-gradient(315deg,transparent 50%,var(--blue) 50%)}
.corner--br{background:linear-gradient(135deg,transparent 50%,var(--blue) 50%)}
.hex{position:absolute;z-index:2}
.sector-bar{position:absolute;left:115px;top:171px;width:316px;height:67px;background:var(--white);display:flex}
.sector{flex:1;display:flex;flex-direction:column;align-items:center;justify-content:center;gap:6px;font-size:6.4px;color:var(--ink)}
.sector--active{background:var(--blue-light)}
.sector svg{width:26px;height:26px}
.footer{position:absolute;left:0;top:269px;width:546px;height:121px;background:var(--footer);color:var(--white)}
.footer-brand{position:absolute;left:40px;top:22px;width:130px;display:flex;flex-direction:column;align-items:center;gap:8px}
.footer-brand .dot{width:38px;height:38px;border-radius:50%;background:var(--blue)}
.footer-brand .name{font-weight:500;font-size:16px;line-height:1.2;color:var(--blue)}
.contact-title{position:absolute;left:196px;top:23px;font-weight:600;font-size:10.5px}
.contact-list,.branch-list{position:absolute;list-style:none;font-size:7px}
.contact-list{left:196px;top:44px}
.branch-list{left:357px;top:25px}
.contact-list li,.branch-list li{display:flex;align-items:center;gap:8px;height:15.2px;white-space:nowrap}
.icon{width:7px;height:7px;flex:none}
.copyright{position:absolute;left:0;width:100%;top:108px;text-align:center;font-size:4.2px;letter-spacing:.1px}
.ref{position:absolute;right:10px;top:109px;font-size:4.2px}
</style>
</head>
<body>
<div class="board">

  <!-- Home: service choice -->
  <section class="screen screen--home">
    <div class="hero">
      <div class="photo photo--solar-field" role="img" aria-label="Solar farm at sunset"></div>
      <div class="photo photo--roof photo--split-right" role="img" aria-label="Roof gutter with autumn leaves"></div>
      <div class="hero-shade"></div>
      <div class="hero-mark hero-mark--white" style="top:40px"><span class="square"></span></div>
      <h1 class="hero-title" style="top:95px;font-size:29px;font-weight:600">Brightleaf</h1>
      <p class="hero-sub" style="top:131px">Australia's fastest growing maintenance contractors</p>

      <div class="choice-card" style="left:118px;top:160px;width:148px">
        <span class="num" style="left:82px;top:6px">01</span>
        <span class="label" style="left:15px;top:30px">SOLAR PANEL CLEANING</span>
        <span class="more" style="left:69px;top:42px">Explore More</span>
      </div>
      <div class="corner corner--tl" style="left:118px;top:160px"></div>
      <div class="choice-card" style="left:251px;top:167px;width:146px">
        <span class="num" style="left:49px;top:13px">02</span>
        <span class="label" style="left:49px;top:38px">GUTTER CLEANING</span>
        <span class="more" style="left:49px;top:50px">Explore More</span>
      </div>
      <div class="corner corner--br" style="left:381px;top:218px"></div>

      <svg class="hex" style="left:226px;top:166px" width="40" height="40" viewBox="0 0 40 40">
        <polygon points="20,1 37,10 37,30 20,39 3,30 3,10" fill="var(--blue)"/>
        <rect x="12" y="13" width="16" height="12" fill="none" stroke="#fff" stroke-width="1.4"/>
        <path d="M12 19h16M17 13v12M23 13v12" stroke="#fff" stroke-width="1"/>
      </svg>
      <svg class="hex" style="left:257px;top:186px" width="34" height="34" viewBox="0 0 40 40">
        <polygon points="20,1 37,10 37,30 20,39 3,30 3,10" fill="#cfe6f8"/>
        <path d="M12 15h14v4H12zM15 22v6M19 22v8M23 22v6" stroke="var(--blue)" stroke-width="1.6" fill="none"/>
      </svg>
    </div>
    <footer class="footer">
      <div class="footer-brand"><span class="dot"></span><span class="name">Brightleaf</span></div>
      <h2 class="contact-title">Contact Us</h2>
      <ul class="contact-list">
        <li><svg class="icon" viewBox="0 0 10 10"><rect x="0" y="2" width="10" height="7" fill="var(--blue)"/></svg>sales@brightleaf.com.au</li>
        <li><svg class="icon" viewBox="0 0 10 10"><rect x="2" y="0" width="6" height="10" fill="var(--blue)"/></svg>Head Office - Kestrel Vale NSW 2580</li>
        <li><svg class="icon" viewBox="0 0 10 10"><rect x="1" y="2" width="7" height="7" fill="none" stroke="var(--blue)" stroke-width="1.3"/></svg>ABN: 48093716552</li>
      </ul>
      <ul class="branch-list">
        <li><svg class="icon" viewBox="0 0 10 10"><circle cx="5" cy="5" r="5" fill="var(--blue)"/><path d="M4 3l2 2-2 2" stroke="#000" stroke-width="1.3" fill="none"/></svg>Sydney – 02 7391 8056</li>
        <li><svg class="icon" viewBox="0 0 10 10"><circle cx="5" cy="5" r="5" fill="var(--blue)"/><path d="M4 3l2 2-2 2" stroke="#000" stroke-width="1.3" fill="none"/></svg>Southern Highlands – 02 4863 1708</li>
        <li><svg class="icon" viewBox="0 0 10 10"><circle cx="5" cy="5" r="5" fill="var(--blue)"/><path d="M4 3l2 2-2 2" stroke="#000" stroke-width="1.3" fill="none"/></svg>Goulburn – 02 4863 1708</li>
        <li><svg class="icon" viewBox="0 0 10 10"><circle cx="5" cy="5" r="5" fill="var(--blue)"/><path d="M4 3l2 2-2 2" stroke="#000" stroke-width="1.3" fill="none"/></svg>Canberra – 02 6172 4385</li>
        <li><svg class="icon" viewBox="0 0 10 10"><circle cx="5" cy="5" r="5" fill="var(--blue)"/><path d="M4 3l2 2-2 2" stroke="#000" stroke-width="1.3" fill="none"/></svg>Wollongong – 02 4239 5817</li>
      </ul>
      <p class="copyright">(C) COPYRIGHT | ALL RIGHTS RESERVED</p>
      <span class="ref">C58</span>
    </footer>
  </section>

  <!-- Gutter cleaning: sector choice -->
  <section class="screen screen--gutter">
    <div class="hero">
      <div class="photo photo--autumn" role="img" aria-label="Worker on a ladder cleaning a roof gutter in autumn light"></div>
      <div class="hero-shade"></div>
      <div class="hero-mark" style="top:60px"><span class="square"></span></div>
      <h1 class="hero-title" style="top:110px;font-size:27px">Gutter Cleaning</h1>
      <p class="hero-sub" style="top:144px">Keep Your Gutters Flowing, Your Home Protecting</p>
      <div class="sector-bar">
        <div class="sector"><svg viewBox="0 0 26 26"><path d="M3 9L13 3l10 6z" fill="var(--blue-deep)"/><rect x="5" y="10" width="3" height="10" fill="var(--blue)"/><rect x="11.5" y="10" width="3" height="10" fill="var(--blue)"/><rect x="18" y="10" width="3" height="10" fill="var(--blue)"/><rect x="3" y="21" width="20" height="3" fill="var(--blue-deep)"/></svg>Government</div>
        <div class="sector sector--active"><svg viewBox="0 0 26 26"><rect x="3" y="8" width="16" height="4" fill="var(--blue)"/><path d="M6 15v6M10 15v8M14 15v6" stroke="var(--blue)" stroke-width="1.6"/><path d="M20 3l1 2 2 1-2 1-1 2-1-2-2-1 2-1z" fill="var(--blue)"/></svg>Strata</div>
        <div class="sector"><svg viewBox="0 0 26 26"><rect x="4" y="9" width="8" height="15" fill="var(--blue)"/><rect x="12" y="3" width="10" height="21" fill="var(--blue-deep)"/><path d="M14 6h2M18 6h2M14 10h2M18 10h2M14 14h2M18 14h2" stroke="#fff" stroke-width="1.4"/></svg>Commercial</div>
        <div class="sector"><svg viewBox="0 0 26 26"><rect x="14" y="4" width="7" height="20" fill="var(--blue-deep)"/><path d="M3 15l7-6 7 6v9H3z" fill="var(--blue)"/><rect x="8" y="18" width="4" height="6" fill="#fff"/></svg>Residential</div>
      </div>
      <div class="corner corner--tl" style="left:115px;top:171px"></div>
      <div class="corner corner--br" style="left:415px;top:222px"></div>
    </div>
    <footer class="footer">
      <div class="footer-brand"><span class="dot"></span><span class="name">Brightleaf</span></div>
      <h2 class="contact-title">Contact Us</h2>
      <ul class="contact-list">
        <li><svg class="icon" viewBox="0 0 10 10"><rect x="0" y="2" width="10" height="7" fill="var(--blue)"/></svg>sales@brightleaf.com.au</li>
        <li><svg class="icon" viewBox="0 0 10 10"><rect x="2" y="0" width="6" height="10" fill="var(--blue)"/></svg>Head Office - Kestrel Vale NSW 2580</li>
        <li><svg class="icon" viewBox="0 0 10 10"><rect x="1" y="2" width="7" height="7" fill="none" stroke="var(--blue)" stroke-width="1.3"/></svg>ABN: 48093716552</li>
      </ul>
      <ul class="branch-list">
        <li><svg class="icon" viewBox="0 0 10 10"><circle cx="5" cy="5" r="5" fill="var(--blue)"/><path d="M4 3l2 2-2 2" stroke="#000" stroke-width="1.3" fill="none"/></svg>Sydney – 02 7391 8056</li>
        <li><svg class="icon" viewBox="0 0 10 10"><circle cx="5" cy="5" r="5" fill="var(--blue)"/><path d="M4 3l2 2-2 2" stroke="#000" stroke-width="1.3" fill="none"/></svg>Southern Highlands – 02 4863 1708</li>
        <li><svg class="icon" viewBox="0 0 10 10"><circle cx="5" cy="5" r="5" fill="var(--blue)"/><path d="M4 3l2 2-2 2" stroke="#000" stroke-width="1.3" fill="none"/></svg>Goulburn – 02 4863 1708</li>
        <li><svg class="icon" viewBox="0 0 10 10"><circle cx="5" cy="5" r="5" fill="var(--blue)"/><path d="M4 3l2 2-2 2" stroke="#000" stroke-width="1.3" fill="none"/></svg>Canberra – 02 6172 4385</li>
        <li><svg class="icon" viewBox="0 0 10 10"><circle cx="5" cy="5" r="5" fill="var(--blue)"/><path d="M4 3l2 2-2 2" stroke="#000" stroke-width="1.3" fill="none"/></svg>Wollongong – 02 4239 5817</li>
      </ul>
      <p class="copyright">(C) COPYRIGHT | ALL RIGHTS RESERVED</p>
      <span class="ref">C58</span>
    </footer>
  </section>

  <!-- Solar panel cleaning: sector choice -->
  <section class="screen screen--solar">
    <div class="hero">
      <div class="photo photo--solar-field" role="img" aria-label="Rows of solar panels under a sunset sky"></div>
      <div class="hero-shade"></div>
      <div class="hero-mark" style="top:60px"><span class="square"></span></div>
      <h1 class="hero-title" style="top:110px;font-size:27px">Solar Panel Cleaning</h1>
      <p class="hero-sub" style="top:144px">Protect Your Investment with Professional Solar Panel Cleaning.</p>
      <div class="sector-bar">
        <div class="sector"><svg viewBox="0 0 26 26"><path d="M3 9L13 3l10 6z" fill="var(--blue-deep)"/><rect x="5" y="10" width="3" height="10" fill="var(--blue)"/><rect x="11.5" y="10" width="3" height="10" fill="var(--blue)"/><rect x="18" y="10" width="3" height="10" fill="var(--blue)"/><rect x="3" y="21" width="20" height="3" fill="var(--blue-deep)"/></svg>Government</div>
        <div class="sector sector--active"><svg viewBox="0 0 26 26"><rect x="4" y="6" width="4" height="9" fill="var(--blue)"/><rect x="10" y="3" width="6" height="12" fill="var(--blue-deep)"/><rect x="18" y="7" width="4" height="8" fill="var(--blue)"/><rect x="2" y="15" width="22" height="2" fill="var(--blue-deep)"/><path d="M7 19a6 5 0 0 0 12 0" stroke="var(--blue)" stroke-width="2" fill="none"/></svg>Infrastructure</div>
        <div class="sector"><svg viewBox="0 0 26 26"><rect x="4" y="9" width="8" height="15" fill="var(--blue)"/><rect x="12" y="3" width="10" height="21" fill="var(--blue-deep)"/><path d="M14 6h2M18 6h2M14 10h2M18 10h2M14 14h2M18 14h2" stroke="#fff" stroke-width="1.4"/></svg>Commercial</div>
        <div class="sector"><svg viewBox="0 0 26 26"><rect x="14" y="4" width="7" height="20" fill="var(--blue-deep)"/><path d="M3 15l7-6 7 6v9H3z" fill="var(--blue)"/><rect x="8" y="18" width="4" height="6" fill="#fff"/></svg>Residential</div>
      </div>
      <div class="corner corner--tl" style="left:115px;top:171px"></div>
      <div class="corner corner--br" style="left:415px;top:222px"></div>
    </div>
    <footer class="footer">
      <div class="footer-brand"><span class="dot"></span><span class="name">Brightleaf</span></div>
      <h2 class="contact-title">Contact Us</h2>
      <ul class="contact-list">
        <li><svg class="icon" viewBox="0 0 10 10"><rect x="0" y="2" width="10" height="7" fill="var(--blue)"/></svg>sales@brightleaf.com.au</li>
        <li><svg class="icon" viewBox="0 0 10 10"><rect x="2" y="0" width="6" height="10" fill="var(--blue)"/></svg>Head Office - Kestrel Vale NSW 2580</li>
        <li><svg class="icon" viewBox="0 0 10 10"><rect x="1" y="2" width="7" height="7" fill="none" stroke="var(--blue)" stroke-width="1.3"/></svg>ABN: 48093716552</li>
      </ul>
      <ul class="branch-list">
        <li><svg class="icon" viewBox="0 0 10 10"><circle cx="5" cy="5" r="5" fill="var(--blue)"/><path d="M4 3l2 2-2 2" stroke="#000" stroke-width="1.3" fill="none"/></svg>Sydney – 02 7391 8056</li>
        <li><svg class="icon" viewBox="0 0 10 10"><circle cx="5" cy="5" r="5" fill="var(--blue)"/><path d="M4 3l2 2-2 2" stroke="#000" stroke-width="1.3" fill="none"/></svg>Southern Highlands – 02 4863 1708</li>
        <li><svg class="icon" viewBox="0 0 10 10"><circle cx="5" cy="5" r="5" fill="var(--blue)"/><path d="M4 3l2 2-2 2" stroke="#000" stroke-width="1.3" fill="none"/></svg>Goulburn – 02 4863 1708</li>
        <li><svg class="icon" viewBox="0 0 10 10"><circle cx="5" cy="5" r="5" fill="var(--blue)"/><path d="M4 3l2 2-2 2" stroke="#000" stroke-width="1.3" fill="none"/></svg>Canberra – 02 6172 4385</li>
        <li><svg class="icon" viewBox="0 0 10 10"><circle cx="5" cy="5" r="5" fill="var(--blue)"/><path d="M4 3l2 2-2 2" stroke="#000" stroke-width="1.3" fill="none"/></svg>Wollongong – 02 4239 5817</li>
      </ul>
      <p class="copyright">(C) COPYRIGHT | ALL RIGHTS RESERVED</p>
      <span class="ref">C58</span>
    </footer>
  </section>

</div>
</body>
</html>
```